KTR Design Business Card

I need to develop a business card for my real estate design and investment company. Something clean, classic and professional with a modern vibe.

Industry/Entity Type

Real Estate

Font styles to use
Serif
Sans Serif

```html
<!DOCTYPE html>
<html lang="en">
<head>
<meta charset="utf-8">
<title>KTR Design Business Card</title>
<link href="https://fonts.googleapis.com/css2?family=Exo+2:wght@300;400;500&display=swap" rel="stylesheet">
<style>
  :root {
    --page: #e9e7e4;
    --card-white: #f7f7f7;
    --card-dark: #333333;
    --sweep-grey: #b9b9b9;
    --ink-dark: #2b2b2b;
    --ink-light: #ffffff;
  }
  html, body {
    margin: 0;
    width: 1200px;
    height: 901px;
    overflow: hidden;
    background: var(--page);
    font-family: "Exo 2", sans-serif;
  }
  .card {
    position: absolute;
    left: 150px;
    top: 193px;
    width: 900px;
    height: 514px;
    border-radius: 42px;
    background: var(--card-white);
    overflow: hidden;
    box-shadow: 0 10px 30px rgba(0,0,0,0.18);
  }
  .card-shapes {
    position: absolute;
    inset: 0;
  }
  .brand {
    position: absolute;
    left: 70px;
    top: 205px;
    width: 330px;
    text-align: center;
    font-weight: 300;
    font-size: 52px;
    letter-spacing: 2px;
    color: var(--ink-dark);
  }
  .details {
    position: absolute;
    right: 58px;
    top: 70px;
    text-align: right;
    color: var(--ink-light);
  }
  .person-name {
    font-size: 27px;
    font-weight: 500;
    letter-spacing: 2px;
    margin: 0;
  }
  .person-role {
    font-size: 18px;
    letter-spacing: 1px;
    margin: 2px 0 0;
  }
  .address {
    font-size: 18px;
    letter-spacing: 1px;
    line-height: 1.35;
    margin: 62px 0 0;
  }
  .contact-list {
    list-style: none;
    margin: 46px 0 0;
    padding: 0;
    font-size: 17px;
    letter-spacing: 1px;
  }
  .contact-list li {
    display: flex;
    justify-content: flex-end;
    align-items: center;
    gap: 10px;
    height: 31px;
  }
  .contact-icon {
    width: 18px;
    height: 18px;
    fill: none;
    stroke: var(--ink-light);
    stroke-width: 1.8;
  }
</style>
</head>
<body>
  <div class="card">
    <svg class="card-shapes" viewBox="0 0 900 514" width="900" height="514" aria-hidden="true">
      <path fill="var(--sweep-grey)" d="M548,0 C505,70 545,150 455,232 C365,314 312,385 312,514 L340,514 C340,390 395,320 480,240 C565,160 525,70 575,0 Z"/>
      <path fill="var(--card-dark)" d="M580,0 C535,70 575,160 490,242 C405,324 352,392 352,514 L900,514 L900,0 Z"/>
    </svg>

    <div class="brand">KTR Design</div>

    <div class="details">
      <p class="person-name">DANIEL MERCER</p>
      <p class="person-role">Managing Director</p>
      <p class="address">27, 6th floor, Harbor Plaza<br>Road</p>
      <ul class="contact-list">
        <li>020 555 0147
          <svg class="contact-icon" viewBox="0 0 24 24"><path d="M5 3h4l2 5-3 2a11 11 0 0 0 6 6l2-3 5 2v4a2 2 0 0 1-2 2A17 17 0 0 1 3 5a2 2 0 0 1 2-2z"/></svg>
        </li>
        <li>020 555 0148
          <svg class="contact-icon" viewBox="0 0 24 24"><rect x="6" y="2" width="12" height="20" rx="2"/><line x1="10" y1="18" x2="14" y2="18"/></svg>
        </li>
        <li>020 555 0149
          <svg class="contact-icon" viewBox="0 0 24 24"><rect x="4" y="9" width="16" height="12" rx="1"/><rect x="7" y="3" width="10" height="6"/><line x1="8" y1="14" x2="16" y2="14"/><line x1="8" y1="17" x2="16" y2="17"/></svg>
        </li>
        <li>hello@ktrdesign.com
          <svg class="contact-icon" viewBox="0 0 24 24"><rect x="3" y="5" width="18" height="14" rx="1"/><path d="M3 6l9 7 9-7"/></svg>
        </li>
        <li>www.ktrdesign.com
          <svg class="contact-icon" viewBox="0 0 24 24"><circle cx="12" cy="12" r="9"/><ellipse cx="12" cy="12" rx="4" ry="9"/><line x1="3" y1="12" x2="21" y2="12"/></svg>
        </li>
      </ul>
    </div>
  </div>
</body>
</html>
```